DPT Brochure

A brochure that depicts what we do here at our personal injury law firm based in California. We help clients that have been involved in motor vehicle accidents, slip and fall, premise liability, wrongful death, and dog bites. We ensure that they obtain quality medical treatment for their injuries that they sustained. We also assist with the repairs to their vehicle and property damage claim at no additional charge. We also specialize in employment law involving wrongful termination, sexual harrasment, hour and wage, labor law violations, etc. We have a website that you can reference www.dptcounsel-example.com. We are looking for a modern sleek design. Not too much color our office colors are black and white. You can incorporate some burgubndy or dark blue.

```html
<!DOCTYPE html>
<html lang="en">
<head>
<meta charset="utf-8">
<title>DPT Counsel – Tri-fold Brochure</title>
<link rel="stylesheet" href="https://fonts.googleapis.com/css2?family=Noto+Serif:wght@400&family=Roboto:wght@300;400;500;700&display=swap">
<style>
:root{
  --backdrop:#7b7b7b;
  --paper:#ffffff;
  --panel-grey:#f2f2f2;
  --ink:#1b1b1b;
  --body:#555555;
  --navy:#1d2638;
  --navy-soft:#2a3650;
  --burgundy:#8e1f22;
  --label:#ffffff;
}
*{box-sizing:border-box;margin:0;padding:0}
html,body{width:1114px;height:1200px;overflow:hidden;background:var(--backdrop)}
.stage{position:absolute;left:0;top:0;width:1848px;height:1992px;transform:scale(0.6028);transform-origin:0 0;font-family:"Roboto",sans-serif;color:var(--ink)}
.side-label{position:absolute;color:var(--label);font:500 22px "Roboto",sans-serif;letter-spacing:14px}
.side-label.vertical{writing-mode:vertical-rl;transform:rotate(180deg)}
.sheet{position:absolute;background:var(--paper);overflow:hidden}
.photo{position:absolute}
.photo-team{background:linear-gradient(180deg,#c9ccd0 0%,#6d6f74 55%,#2a2a2e 100%)}
.photo-crash{background:linear-gradient(100deg,#1a2230 0%,#2c3b52 35%,#5d7fa3 60%,#9fbfdc 80%,#c9c6a2 100%)}
.photo-crash-cover{background:linear-gradient(100deg,#1f2a3a 0%,#3b5677 45%,#8fb2d3 75%,#cfc89a 100%)}
.photo-car-back{background:linear-gradient(160deg,#c9c088 0%,#44556c 30%,#1c2432 65%,#2c323c 100%)}
.rule{position:absolute;height:8px;background:#0d0d0d;border-radius:4px}
.brand{position:absolute;text-align:center;font:400 44px "Noto Serif",serif;color:var(--ink);letter-spacing:3px;line-height:1;white-space:nowrap}
.serif-title{position:absolute;text-align:center;font:400 29px/1.12 "Noto Serif",serif;color:var(--ink)}
.copy{position:absolute;text-align:center;font:300 13px/1.16 "Roboto",sans-serif;color:var(--body);letter-spacing:-0.1px}
.lead{position:absolute;text-align:center;font:300 17px/1.25 "Roboto",sans-serif;color:var(--ink)}
.dashes{position:absolute;font:300 18px "Roboto",sans-serif;letter-spacing:4px;color:#333}
.badge{position:absolute;height:66px;border-radius:3px}
.badge.plaque{background:linear-gradient(#5a2a1a,#2a140c);border:2px solid #b08a4a}
.badge.ribbon{background:#f4f1ea;border:1px solid #c8c1ad}
.badge.card{background:#4b4b4b;border-radius:6px}
.locations{position:absolute;width:330px}
.location{display:flex;align-items:center;height:50px}
.location .city{display:flex;align-items:center;gap:6px;width:112px;flex:none;white-space:nowrap;font:500 14px "Roboto",sans-serif;color:var(--ink)}
.location .addr{border-left:1px solid #999;padding-left:10px;font:300 12.5px/1.25 "Roboto",sans-serif;color:#666;white-space:nowrap}
.cta{position:absolute;width:297px;height:64px;background:var(--navy);display:flex;color:#fff;overflow:hidden}
.cta .cta-icon{width:64px;height:64px;flex:none;background:var(--navy-soft);display:flex;align-items:center;justify-content:center}
.cta .cta-text{padding:9px 0 0 18px;line-height:1;white-space:nowrap}
.cta .cta-kicker{font:400 14px "Roboto",sans-serif}
.cta .cta-number{font:700 30px "Roboto",sans-serif;letter-spacing:0.3px;margin-top:4px}
.url{position:absolute;text-align:center;font:400 12.5px "Noto Serif",serif;letter-spacing:3.6px;color:#333}
.band{position:absolute;left:0;top:0;width:1121px;height:204px;background:linear-gradient(90deg,#101a2b 0%,#1c2940 40%,#25324a 70%,#1a2538 100%)}
.band-title{position:absolute;left:172px;top:78px;font:400 56px "Noto Serif",serif;color:#fff;letter-spacing:1px}
.col-grey{position:absolute;background:var(--panel-grey)}
.service-icon{position:absolute;width:84px;height:84px;border-radius:50%;background:var(--navy)}
.service-name{position:absolute;font:300 24px/1.2 "Roboto",sans-serif;color:var(--ink)}
.service-copy{position:absolute;font:300 12.5px/1.18 "Roboto",sans-serif;color:#5a5a5a;letter-spacing:-0.1px}
.promise{position:absolute;display:flex;gap:10px;width:290px;font:300 15.5px/1.15 "Roboto",sans-serif;color:#333}
.promise svg{flex:none;margin-top:2px}
.offer{position:absolute;text-align:center;font:500 25px "Roboto",sans-serif;color:var(--burgundy);letter-spacing:0.3px}
</style>
</head>
<body>
<div class="stage">

  <div class="side-label" style="left:618px;top:60px">OUTSIDE</div>
  <div class="side-label" style="left:618px;top:998px">INSIDE</div>
  <div class="side-label vertical" style="left:1717px;top:440px">COVER</div>
  <div class="side-label vertical" style="left:1717px;top:1420px">BACK</div>

  <!-- Outside spread -->
  <section class="sheet outside" style="left:118px;top:97px;width:1121px;height:872px">
    <div class="photo photo-team" style="left:0;top:0;width:370px;height:198px" role="img" aria-label="Group photo of the firm's attorneys and staff in the office"></div>
    <div class="rule" style="left:0;top:203px;width:688px"></div>

    <div class="brand" style="left:374px;top:80px;width:374px">DPT COUNSEL</div>
    <div class="brand" style="left:748px;top:80px;width:374px">DPT COUNSEL</div>

    <div class="photo photo-crash" style="left:370px;top:219px;width:751px;height:350px" role="img" aria-label="Two cars with crumpled fronts after a collision"></div>
    <div class="rule" style="left:917px;top:575px;width:210px"></div>

    <h2 class="serif-title" style="left:30px;top:246px;width:314px">DPT Counsel<br>Team</h2>
    <p class="copy" style="left:30px;top:326px;width:314px">A premier California law firm, DPT Counsel takes on the powerful to get our clients the justice and compensation they deserve. When tragedy happens, you need an experienced team to navigate the justice system and ensure you receive everything you are entitled to. The award-winning DPT Counsel team will work with you and will stand beside you every step of the way.</p>
    <p class="lead" style="left:24px;top:470px;width:326px">We will work with you to get you the justice and compensation you deserve.</p>
    <div class="dashes" style="left:124px;top:544px">-----------</div>
    <h3 class="serif-title" style="left:30px;top:593px;width:314px;font-size:24px">Experience matters.</h3>
    <p class="copy" style="left:40px;top:634px;width:298px">Representing victims of car accidents, slip and fall injuries, workplace harassment, sexual assault, and more. DPT Counsel gets clients the justice and the compensation they deserve. When you choose to work with DPT Counsel, our award-winning attorneys will stand beside you every step of the way.</p>
    <div class="badge plaque" style="left:59px;top:758px;width:44px"></div>
    <div class="badge ribbon" style="left:119px;top:758px;width:64px"></div>
    <div class="badge card" style="left:192px;top:758px;width:80px"></div>
    <div class="badge plaque" style="left:280px;top:758px;width:44px"></div>

    <div class="locations" style="left:420px;top:590px">
      <div class="location"><span class="city"><svg width="12" height="14" viewBox="0 0 12 14"><path d="M6 13s5-4.6 5-8A5 5 0 0 0 1 5c0 3.4 5 8 5 8z" fill="none" stroke="#222" stroke-width="1.3"/><circle cx="6" cy="5" r="1.8" fill="none" stroke="#222" stroke-width="1.3"/></svg>Los Angeles</span><span class="addr">2210 Marlow Ave. Suite: 140<br>Los Angeles, CA 90017</span></div>
      <div class="location"><span class="city"><svg width="12" height="14" viewBox="0 0 12 14"><path d="M6 13s5-4.6 5-8A5 5 0 0 0 1 5c0 3.4 5 8 5 8z" fill="none" stroke="#222" stroke-width="1.3"/><circle cx="6" cy="5" r="1.8" fill="none" stroke="#222" stroke-width="1.3"/></svg>Victorville</span><span class="addr">8810 Pinecrest Rd.<br>Victorville, CA 92395</span></div>
      <div class="location"><span class="city"><svg width="12" height="14" viewBox="0 0 12 14"><path d="M6 13s5-4.6 5-8A5 5 0 0 0 1 5c0 3.4 5 8 5 8z" fill="none" stroke="#222" stroke-width="1.3"/><circle cx="6" cy="5" r="1.8" fill="none" stroke="#222" stroke-width="1.3"/></svg>Turlock</span><span class="addr">412 W. Alder St.<br>Turlock, CA 95382</span></div>
    </div>

    <div class="cta" style="left:410px;top:760px">
      <div class="cta-icon"><svg width="24" height="38" viewBox="0 0 24 38"><rect x="1.5" y="1.5" width="21" height="35" rx="4" fill="none" stroke="#fff" stroke-width="2"/><line x1="1.5" y1="29" x2="22.5" y2="29" stroke="#fff" stroke-width="2"/></svg></div>
      <div class="cta-text"><div class="cta-kicker">Talk to a Lawyer Today</div><div class="cta-number">800.555.0142</div></div>
    </div>
    <div class="url" style="left:374px;top:833px;width:374px">dptcounsel-example.com</div>

    <h2 class="serif-title" style="left:760px;top:630px;width:350px">DPT Counsel<br>Award-Winning<br>Injury Attorneys</h2>
    <div class="cta" style="left:780px;top:760px">
      <div class="cta-icon"><svg width="24" height="38" viewBox="0 0 24 38"><rect x="1.5" y="1.5" width="21" height="35" rx="4" fill="none" stroke="#fff" stroke-width="2"/><line x1="1.5" y1="29" x2="22.5" y2="29" stroke="#fff" stroke-width="2"/></svg></div>
      <div class="cta-text"><div class="cta-kicker">Talk to a Lawyer Today</div><div class="cta-number">800.555.0142</div></div>
    </div>
    <div class="url" style="left:748px;top:833px;width:374px">dptcounsel-example.com</div>
  </section>

  <!-- Cover panel -->
  <section class="sheet cover" style="left:1314px;top:97px;width:384px;height:878px">
    <div class="brand" style="left:0;top:84px;width:384px">DPT COUNSEL</div>
    <div class="photo photo-crash-cover" style="left:0;top:220px;width:384px;height:353px" role="img" aria-label="Two cars with crumpled fronts after a collision"></div>
    <div class="rule" style="left:179px;top:579px;width:210px"></div>
    <h2 class="serif-title" style="left:17px;top:636px;width:350px">DPT Counsel<br>Award-Winning<br>Injury Attorneys</h2>
    <div class="cta" style="left:42px;top:766px;width:299px">
      <div class="cta-icon"><svg width="24" height="38" viewBox="0 0 24 38"><rect x="1.5" y="1.5" width="21" height="35" rx="4" fill="none" stroke="#fff" stroke-width="2"/><line x1="1.5" y1="29" x2="22.5" y2="29" stroke="#fff" stroke-width="2"/></svg></div>
      <div class="cta-text"><div class="cta-kicker">Talk to a Lawyer Today</div><div class="cta-number">800.555.0142</div></div>
    </div>
    <div class="url" style="left:0;top:840px;width:384px">dptcounsel-example.com</div>
  </section>

  <!-- Inside spread -->
  <section class="sheet inside" style="left:118px;top:1039px;width:1121px;height:871px">
    <div class="col-grey" style="left:750px;top:204px;width:371px;height:367px"></div>
    <div class="band" role="img" aria-label="Dark blue tinted photo of a lawyer signing documents at a desk"></div>
    <h1 class="band-title">Areas of Practice</h1>
    <div class="rule" style="left:0;top:208px;width:677px"></div>

    <div class="service-icon" style="left:47px;top:254px" role="img" aria-label="Icon of a person struck by a car"></div>
    <h3 class="service-name" style="left:148px;top:266px">Motor vehicle<br>accidents</h3>
    <p class="service-copy" style="left:52px;top:350px;width:302px">Moto vehicle accidents often result in property damage, injury, even death. Factors contributing to the risk of collisions include vehicle design, speed of operation, road design, road environment, driver skill, impairment due to alcohol or drugs, and behavior, notably distracted driving, speeding and street racing.</p>

    <div class="service-icon" style="left:414px;top:254px" role="img" aria-label="Icon of a person slipping and falling"></div>
    <h3 class="service-name" style="left:514px;top:266px">Slip &amp; Fall<br>Accidents</h3>
    <p class="service-copy" style="left:419px;top:350px;width:300px">A property owner's failure to properly maintain his or her property and keep it free from hazards (poor lighting, uneven walkways, spills, unsafe structures or ceilings) can result in a personal injury. Even poor security on the part of the property owner, which results in injury, can result in a slip and fall claim.</p>

    <div class="service-icon" style="left:47px;top:464px" role="img" aria-label="Icon of a person carrying a money bag"></div>
    <h3 class="service-name" style="left:148px;top:476px">Premise<br>liability</h3>
    <p class="service-copy" style="left:52px;top:560px;width:302px">Public utility companies have a duty to ensure the safety of the people living in the areas they serve, and when they fail to meet that duty, they can put the health and lives of millions of people at risk. This includes injuries or loss from wildfires caused by a utility's negligence or misconduct.</p>

    <div class="service-icon" style="left:414px;top:464px" role="img" aria-label="Icon of a judge's gavel"></div>
    <h3 class="service-name" style="left:514px;top:476px">Wrongful<br>death</h3>
    <p class="service-copy" style="left:419px;top:560px;width:300px">Wrongful death happens when a person is killed because of another person or entity's negligence or misconduct. DPT Counsel has extensive experience representing and seeking justice for loved ones of a person wrongfully killed.</p>

    <div class="service-icon" style="left:47px;top:664px" role="img" aria-label="Icon of a person with a dog"></div>
    <h3 class="service-name" style="left:148px;top:688px">Dog Bite Injuries</h3>
    <p class="service-copy" style="left:52px;top:760px;width:660px">If you have been bitten or otherwise injured by a domestic animal you may be entitled to compensation for your injuries and emotional distress. The California Civil Code makes pet owners legally responsible for injuries caused by their pets when a dog/animal bite occurs in public or when the victim was lawfully in the space where the bite or attack occurred (not trespassing). DPT Counsel has recovered millions of dollars representing victims of animal bites and attacks.</p>

    <div class="promise" style="left:787px;top:269px"><svg width="20" height="20" viewBox="0 0 20 20"><circle cx="10" cy="10" r="8" fill="none" stroke="var(--burgundy)" stroke-width="1.8"/><path d="M5.5 10l3.5 3.5L18 3" fill="none" stroke="var(--burgundy)" stroke-width="2.2"/></svg><span>We ensure that they obtain quality medical treatment for their injuries that they sustained.</span></div>
    <div class="promise" style="left:787px;top:360px"><svg width="20" height="20" viewBox="0 0 20 20"><circle cx="10" cy="10" r="8" fill="none" stroke="var(--burgundy)" stroke-width="1.8"/><path d="M5.5 10l3.5 3.5L18 3" fill="none" stroke="var(--burgundy)" stroke-width="2.2"/></svg><span>We also assist with the repairs to their vehicle and property damage claim at no additional charge.</span></div>
    <div class="promise" style="left:787px;top:451px"><svg width="20" height="20" viewBox="0 0 20 20"><circle cx="10" cy="10" r="8" fill="none" stroke="var(--burgundy)" stroke-width="1.8"/><path d="M5.5 10l3.5 3.5L18 3" fill="none" stroke="var(--burgundy)" stroke-width="2.2"/></svg><span>We also specialize in employment law involving wrongful termination, sexual harrasment, hour and wage, labor law violations, etc</span></div>

    <div class="brand" style="left:750px;top:620px;width:380px;font-size:40px">DPT COUNSEL</div>
    <div class="offer" style="left:750px;top:704px;width:380px">GET FREE LEGAL ADVICE</div>
    <div class="cta" style="left:783px;top:741px">
      <div class="cta-icon"><svg width="24" height="38" viewBox="0 0 24 38"><rect x="1.5" y="1.5" width="21" height="35" rx="4" fill="none" stroke="#fff" stroke-width="2"/><line x1="1.5" y1="29" x2="22.5" y2="29" stroke="#fff" stroke-width="2"/></svg></div>
      <div class="cta-text"><div class="cta-kicker">Talk to a Lawyer Today</div><div class="cta-number">800.555.0142</div></div>
    </div>
    <div class="url" style="left:750px;top:814px;width:380px">dptcounsel-example.com</div>
  </section>

  <!-- Back panel -->
  <section class="sheet back" style="left:1314px;top:1034px;width:373px;height:881px">
    <div class="brand" style="left:0;top:82px;width:373px">DPT COUNSEL</div>
    <div class="rule" style="left:0;top:205px;width:322px"></div>
    <div class="photo photo-car-back" style="left:0;top:220px;width:373px;height:354px" role="img" aria-label="Close-up of a dark blue car's damaged front end"></div>
    <div class="locations" style="left:50px;top:597px">
      <div class="location"><span class="city"><svg width="12" height="14" viewBox="0 0 12 14"><path d="M6 13s5-4.6 5-8A5 5 0 0 0 1 5c0 3.4 5 8 5 8z" fill="none" stroke="#222" stroke-width="1.3"/><circle cx="6" cy="5" r="1.8" fill="none" stroke="#222" stroke-width="1.3"/></svg>Los Angeles</span><span class="addr">2210 Marlow Ave. Suite: 140<br>Los Angeles, CA 90017</span></div>
      <div class="location"><span class="city"><svg width="12" height="14" viewBox="0 0 12 14"><path d="M6 13s5-4.6 5-8A5 5 0 0 0 1 5c0 3.4 5 8 5 8z" fill="none" stroke="#222" stroke-width="1.3"/><circle cx="6" cy="5" r="1.8" fill="none" stroke="#222" stroke-width="1.3"/></svg>Victorville</span><span class="addr">8810 Pinecrest Rd.<br>Victorville, CA 92395</span></div>
      <div class="location"><span class="city"><svg width="12" height="14" viewBox="0 0 12 14"><path d="M6 13s5-4.6 5-8A5 5 0 0 0 1 5c0 3.4 5 8 5 8z" fill="none" stroke="#222" stroke-width="1.3"/><circle cx="6" cy="5" r="1.8" fill="none" stroke="#222" stroke-width="1.3"/></svg>Turlock</span><span class="addr">412 W. Alder St.<br>Turlock, CA 95382</span></div>
    </div>
    <div class="cta" style="left:41px;top:768px;width:300px">
      <div class="cta-icon"><svg width="24" height="38" viewBox="0 0 24 38"><rect x="1.5" y="1.5" width="21" height="35" rx="4" fill="none" stroke="#fff" stroke-width="2"/><line x1="1.5" y1="29" x2="22.5" y2="29" stroke="#fff" stroke-width="2"/></svg></div>
      <div class="cta-text"><div class="cta-kicker">Talk to a Lawyer Today</div><div class="cta-number">800.555.0142</div></div>
    </div>
    <div class="url" style="left:0;top:841px;width:373px">dptcounsel-example.com</div>
  </section>

</div>
</body>
</html>
```